Every Shelf Set Neatly or ESN Organized needs a business card design. ESN Organized is a professi

We need a business card design that is clean, sharp and conveys a sense of organization. I already have a logo.

Target Market(s)

Families (specifically mothers), small business owners, parents, seniors

Industry/Entity Type

Business

Contact Information for Business Card

My website is www.esnorganized-example.com and my Facebook page is http://www.sociallink-example.com/everyshelfsetneatly. The phone number is 418-552-7094 and I want to be listed as Lorna M. Pelham, Owner

Requirements
Must have
• My logo.

```html
<!DOCTYPE html>
<html lang="en">
<head>
<meta charset="utf-8">
<title>ESN Organized – Business Card</title>
<link rel="stylesheet" href="https://fonts.googleapis.com/css2?family=Montserrat:wght@400;500&display=swap">
<style>
  :root {
    --backdrop: #2a2a2a;
    --card-dark: #000000;
    --card-light: #efefed;
    --brand-blue: #1a7fd6;
    --text-light: #e6e6e6;
    --text-dark: #1b1b1b;
    --divider: #5a5a5a;
  }
  html, body {
    margin: 0;
    padding: 0;
    width: 1200px;
    height: 840px;
    overflow: hidden;
    background: var(--backdrop);
    font-family: "Montserrat", Arial, sans-serif;
  }
  .canvas {
    position: relative;
    width: 1200px;
    height: 840px;
  }
  .card {
    position: absolute;
    left: 384px;
    width: 459px;
    height: 262px;
  }
  .card--front { top: 121px; background: var(--card-dark); }
  .card--back  { top: 442px; background: var(--card-light); }

  .brand-mark {
    position: absolute;
    left: 16px;
    top: 26px;
    font-size: 40px;
    font-weight: 400;
    line-height: 44px;
    letter-spacing: 1px;
    color: var(--brand-blue);
  }
  .header-divider {
    position: absolute;
    left: 117px;
    top: 24px;
    width: 1px;
    height: 48px;
    background: var(--divider);
  }
  .owner-name {
    position: absolute;
    left: 132px;
    top: 29px;
    margin: 0;
    font-size: 18px;
    font-weight: 400;
    letter-spacing: 0.5px;
    color: var(--brand-blue);
  }
  .owner-title {
    position: absolute;
    left: 132px;
    top: 52px;
    margin: 0;
    font-size: 13px;
    font-weight: 400;
    letter-spacing: 0.6px;
    color: var(--text-light);
  }
  .contact-list {
    position: absolute;
    right: 20px;
    top: 185px;
    margin: 0;
    padding: 0;
    list-style: none;
  }
  .contact-item {
    display: flex;
    justify-content: flex-end;
    align-items: center;
    height: 19.5px;
    font-size: 13px;
    letter-spacing: 0.4px;
    color: var(--text-light);
  }
  .contact-icon {
    width: 12px;
    height: 12px;
    margin-left: 9px;
    flex: none;
  }
  .back-lockup {
    position: absolute;
    inset: 0;
    display: flex;
    align-items: center;
    justify-content: center;
    font-size: 19px;
    font-weight: 500;
    letter-spacing: 3px;
    text-transform: uppercase;
    color: var(--text-dark);
  }
</style>
</head>
<body>
<div class="canvas">
  <section class="card card--front" aria-label="Business card front">
    <div class="brand-mark">ESN</div>
    <div class="header-divider"></div>
    <h1 class="owner-name">Lorna M. Pelham</h1>
    <p class="owner-title">Owner</p>
    <ul class="contact-list">
      <li class="contact-item">418-552-7094
        <svg class="contact-icon" viewBox="0 0 24 24" aria-hidden="true">
          <path fill="#1a7fd6" d="M6.6 10.8a15.2 15.2 0 0 0 6.6 6.6l2.2-2.2a1 1 0 0 1 1-.25 11.4 11.4 0 0 0 3.6.57 1 1 0 0 1 1 1V20a1 1 0 0 1-1 1A17 17 0 0 1 3 4a1 1 0 0 1 1-1h3.5a1 1 0 0 1 1 1c0 1.25.2 2.45.57 3.57a1 1 0 0 1-.25 1z"/>
        </svg>
      </li>
      <li class="contact-item">www.esnorganized-example.com
        <svg class="contact-icon" viewBox="0 0 24 24" aria-hidden="true">
          <circle cx="12" cy="12" r="11" fill="#1a7fd6"/>
          <path fill="none" stroke="#000" stroke-width="1.6" d="M1 12h22M12 1c3 3 4.5 7 4.5 11S15 20 12 23M12 1c-3 3-4.5 7-4.5 11S9 20 12 23"/>
        </svg>
      </li>
      <li class="contact-item">everyshelfsetneatly
        <svg class="contact-icon" viewBox="0 0 24 24" aria-hidden="true">
          <rect x="1" y="1" width="22" height="22" fill="#1a7fd6"/>
        </svg>
      </li>
    </ul>
  </section>

  <section class="card card--back" aria-label="Business card back">
    <div class="back-lockup">Every Shelf Set Neatly</div>
  </section>
</div>
</body>
</html>
```